Business Card for Fashion House

We need a business card design for our personalize fashion service for our customers. the business card should reflect reliability, luxury and creativity.
The brand Gravetto is extracted from "Graceful Velvetto"; Gravetto provides fashion designs sprinkled with luxury and style tailored for our elite clients character profile.
Gravetto is created for those who embody class and elegance with a passion for style.
Target Market(s)
Affluent Customers
Industry/Entity Type
Fashion
Contact Information for Business Card
Samira Haddadin
Fashion Designer
Telephone: +971 4 555 0192
Mobile +971 50 555 0147
Emal info@gravetto-example.com
Website www.gravetto-example.com
Social Media Youtube g+ Facebook Instagram Pin /gravetto
Font styles to use
Other font styles liked:
- Audrey provided
Look and feel
Each slider illustrates characteristics of the customer's brand and the style your logo design should communicate.

```html
<!DOCTYPE html>
<html lang="en">
<head>
<meta charset="utf-8">
<title>Gravetto Business Card</title>
<link href="https://fonts.googleapis.com/css2?family=Marcellus&display=swap" rel="stylesheet">
<style>
  :root {
    --page: #d9d9db;
    --card: #000000;
    --ink: #ffffff;
    --shadow: rgba(0, 0, 0, 0.35);
  }
  * { margin: 0; padding: 0; box-sizing: border-box; }
  html, body {
    width: 1200px;
    height: 1200px;
    overflow: hidden;
    background: var(--page);
    font-family: "Marcellus", serif;
    color: var(--ink);
  }
  .canvas { position: relative; width: 1200px; height: 1200px; }
  .card {
    position: absolute;
    top: 453px;
    width: 525px;
    height: 300px;
    background: var(--card);
    box-shadow: 6px 6px 6px var(--shadow);
    overflow: hidden;
  }
  .card--front { left: 49px; }
  .card--back { left: 630px; }

  .wordmark {
    position: absolute;
    letter-spacing: 0.35em;
    text-transform: uppercase;
    line-height: 1;
  }
  .card--front .wordmark { left: 40px; top: 98px; font-size: 19px; }
  .card--back .wordmark { right: 40px; top: 118px; font-size: 27px; letter-spacing: 0.3em; margin-right: -0.3em; }

  .person { position: absolute; left: 40px; top: 140px; }
  .person__name { font-size: 16px; text-transform: uppercase; letter-spacing: 0.02em; line-height: 1.1; }
  .person__role { font-size: 11px; line-height: 1.3; }

  .contacts { position: absolute; left: 40px; top: 191px; list-style: none; }
  .contacts li {
    display: flex; align-items: center; gap: 9px;
    font-size: 12px; height: 19.5px; letter-spacing: 0.03em;
  }
  .contacts svg { width: 12px; height: 12px; flex: none; }

  .social {
    position: absolute; right: 40px; top: 156px;
    display: flex; align-items: center; gap: 8px;
    font-size: 15px; letter-spacing: 0.08em;
  }
  .social__dot { width: 22px; height: 22px; border-radius: 50%; background: var(--ink); }

  .website {
    position: absolute; right: 40px; top: 256px;
    font-size: 13px; letter-spacing: 0.12em;
  }
</style>
</head>
<body>
<main class="canvas">
  <section class="card card--front" aria-label="Card front">
    <div class="wordmark">Gravetto</div>
    <div class="person">
      <p class="person__name">Samira Haddadin</p>
      <p class="person__role">Fashion Designer</p>
    </div>
    <ul class="contacts">
      <li>
        <svg viewBox="0 0 12 12"><circle cx="6" cy="6" r="6" fill="#fff"/><path d="M3.5 4.5h5v4h-5z" fill="#000"/><circle cx="6" cy="6.5" r="1" fill="#fff"/></svg>
        +971 50 555 0147
      </li>
      <li>
        <svg viewBox="0 0 12 12"><circle cx="6" cy="6" r="6" fill="#fff"/><rect x="4" y="2.8" width="4" height="6.4" rx="0.8" fill="#000"/><rect x="4.8" y="3.7" width="2.4" height="3.8" fill="#fff"/></svg>
        +971 4 555 0192
      </li>
      <li>
        <svg viewBox="0 0 12 12"><circle cx="6" cy="6" r="6" fill="#fff"/><rect x="3" y="4" width="6" height="4.2" fill="#000"/><path d="M3 4l3 2.3L9 4" stroke="#fff" stroke-width="0.7" fill="none"/></svg>
        info@gravetto-example.com
      </li>
      <li>
        <svg viewBox="0 0 12 12"><circle cx="6" cy="6" r="6" fill="#fff"/><circle cx="6" cy="6" r="3.3" fill="none" stroke="#000" stroke-width="0.8"/><path d="M2.7 6h6.6M6 2.7v6.6" stroke="#000" stroke-width="0.7"/></svg>
        www.gravetto-example.com
      </li>
    </ul>
  </section>

  <section class="card card--back" aria-label="Card back">
    <div class="wordmark">Gravetto</div>
    <div class="social"><span class="social__dot"></span>/gravetto</div>
    <div class="website">www.gravetto-example.com</div>
  </section>
</main>
</body>
</html>
```